jQuery Mobile CSS for web app

Task Outline:
Create jQuery Mobile themeroller compliant CSS and icons for a mobile web app.
Task Description:
Brindle Solutions are in the process of implementing a new, web based version of their Tessel operations platform.
The web based version of Tessel is built on top of the jQuery Mobile platform and we are looking for a designer to create a jQuery Mobile themeroller compliant CSS theme pack that we can plug into our application. The aim is to remove the standard jQuery Mobile look and feel and to introduce the Brindle branding throughout the new web app.
A number of screenshots are shown in the attached design spec (brindle_solutions.pdf) that show what the current (Windows Mobile 6.5) application looks like, alongside the development version of our new web app.
Deliverables:
• jQuery Mobile (v 1.4.2) themeroller compliant CSS which provides theming for all jQuery Mobile UI components.
• Example html showing how to use the CSS theme (especially where additional html/css classes are required).
• New set of status icons (as listed in attachment)
Inspiration:
See our website for current branding: www.brindle-solutions-demo.net

```html
<!DOCTYPE html>
<html lang="en">
<head>
<meta charset="utf-8">
<title>Brindle Tessel – Labor</title>
<link rel="stylesheet" href="https://fonts.googleapis.com/css2?family=Open+Sans:wght@400&family=Roboto:wght@400&display=swap">
<style>
  :root {
    --brand-red: #d0161f;
    --header-bg: #000000;
    --header-text: #ffffff;
    --menu-btn: #7a7a7a;
    --menu-icon: #3f4a5a;
    --section-bg: #e8e8e8;
    --list-bg: #f4f4f4;
    --divider: #e2e2e2;
    --text: #555555;
    --nav-icon: #5c6b80;
  }
  * { box-sizing: border-box; margin: 0; padding: 0; }
  html, body { width: 954px; height: 1200px; overflow: hidden; background: var(--list-bg); }
  body { font-family: "Open Sans", sans-serif; color: var(--text); position: relative; }

  .app-header {
    position: absolute; left: 0; top: 0; width: 954px; height: 190px;
    background: var(--header-bg); overflow: hidden;
  }
  .brand-dot {
    position: absolute; left: -70px; top: 40px; width: 150px; height: 150px;
    border-radius: 50%; background: var(--brand-red);
  }
  .app-title {
    position: absolute; left: 244px; top: 64px;
    font-family: "Roboto", sans-serif; font-size: 52px; line-height: 60px;
    color: var(--header-text); font-weight: 400;
  }
  .menu-button {
    position: absolute; left: 803px; top: 56px; width: 86px; height: 84px;
    background: var(--menu-btn); border-radius: 8px;
    display: flex; align-items: center; justify-content: center;
  }

  .section-title {
    position: absolute; left: 0; top: 190px; width: 954px; height: 164px;
    background: var(--section-bg);
    font-size: 50px; color: var(--brand-red);
    padding-left: 50px; line-height: 164px;
  }

  .labor-list { position: absolute; left: 0; top: 354px; width: 954px; list-style: none; }
  .labor-item {
    height: 155px; display: flex; align-items: center;
    border-bottom: 2px solid var(--divider); background: var(--list-bg);
    font-size: 40px;
  }
  .labor-item:last-child { border-bottom: none; height: 160px; }
  .labor-item svg { margin-left: 48px; margin-right: 48px; flex: none; }

  .footer-nav {
    position: absolute; left: 0; top: 994px; width: 954px; height: 206px;
    display: flex; border-top: 2px solid var(--divider); background: var(--list-bg);
  }
  .nav-item {
    flex: 1; display: flex; flex-direction: column; align-items: center;
    padding-top: 36px; font-size: 40px; letter-spacing: 0.5px;
    border-right: 2px solid var(--divider);
  }
  .nav-item:last-child { border-right: none; }
  .nav-item span { margin-top: 18px; }
</style>
</head>
<body>
  <header class="app-header">
    <div class="brand-dot"></div>
    <h1 class="app-title">Brindle Tessel</h1>
    <div class="menu-button">
      <svg width="34" height="26" viewBox="0 0 34 26">
        <rect x="0" y="2" width="34" height="4" fill="var(--menu-icon)"/>
        <rect x="0" y="11" width="34" height="4" fill="var(--menu-icon)"/>
        <rect x="0" y="20" width="34" height="4" fill="var(--menu-icon)"/>
      </svg>
    </div>
  </header>

  <h2 class="section-title">Labor</h2>

  <ul class="labor-list">
    <li class="labor-item"><svg width="46" height="46" viewBox="0 0 46 46"><circle cx="23" cy="23" r="23" fill="var(--brand-red)"/><path d="M13 24 L20 31 L33 17" fill="none" stroke="#fff" stroke-width="5" stroke-linecap="round" stroke-linejoin="round"/></svg>2 X Field Foreman</li>
    <li class="labor-item"><svg width="46" height="46" viewBox="0 0 46 46"><circle cx="23" cy="23" r="23" fill="var(--brand-red)"/><path d="M13 24 L20 31 L33 17" fill="none" stroke="#fff" stroke-width="5" stroke-linecap="round" stroke-linejoin="round"/></svg>1 X Master Electrician</li>
    <li class="labor-item"><svg width="46" height="46" viewBox="0 0 46 46"><circle cx="23" cy="23" r="23" fill="var(--brand-red)"/><path d="M13 24 L20 31 L33 17" fill="none" stroke="#fff" stroke-width="5" stroke-linecap="round" stroke-linejoin="round"/></svg>2 X Field Supervisor</li>
    <li class="labor-item"><svg width="46" height="46" viewBox="0 0 46 46"><circle cx="23" cy="23" r="23" fill="var(--brand-red)"/><path d="M13 24 L20 31 L33 17" fill="none" stroke="#fff" stroke-width="5" stroke-linecap="round" stroke-linejoin="round"/></svg>10 X Pusher</li>
  </ul>

  <nav class="footer-nav">
    <div class="nav-item">
      <svg width="70" height="70" viewBox="0 0 70 70"><circle cx="35" cy="35" r="32" fill="none" stroke="var(--brand-red)" stroke-width="5"/><path d="M19 35 L32 24 L32 31 L50 31 L50 39 L32 39 L32 46 Z" fill="var(--brand-red)"/></svg>
      <span>BACK</span>
    </div>
    <div class="nav-item">
      <svg width="70" height="70" viewBox="0 0 70 70"><g fill="var(--nav-icon)"><rect x="10" y="14" width="8" height="8"/><rect x="22" y="14" width="40" height="8"/><rect x="10" y="31" width="8" height="8"/><rect x="22" y="31" width="40" height="8"/><rect x="10" y="48" width="8" height="8"/><rect x="22" y="48" width="40" height="8"/></g></svg>
      <span>TASKS</span>
    </div>
    <div class="nav-item">
      <svg width="70" height="70" viewBox="0 0 70 70"><circle cx="35" cy="35" r="32" fill="none" stroke="var(--brand-red)" stroke-width="5"/><path d="M51 35 L38 24 L38 31 L20 31 L20 39 L38 39 L38 46 Z" fill="var(--brand-red)"/></svg>
      <span>NEXT</span>
    </div>
  </nav>
</body>
</html>
```